A start up special flyer design!

Hi All - Have updated the attachment content - This is the info required for the designs.
I need a catchy flyer to send out to a few areas to advertise the start of my plumbing business!
The flyer will contain an offer for customers, which will need to have some key details on it. See attached. Feel free to fit these criteria into the flyer given your knowledge on design and messaging principles. Key thing to get across to customers is the discount and special offer, and that it is a start up offer.
I have a logo that needs to be on the flyer as well - let me know what format you require and I will send through to you.
The color scheme needs to be blue / grey / black / white.
Let me know if you have any questions.
I

```html
<!DOCTYPE html>
<html lang="en">
<head>
<meta charset="utf-8">
<title>Danny Flow Plumbing – Start Up Flyer and Business Cards</title>
<link rel="stylesheet" href="https://fonts.googleapis.com/css2?family=Roboto+Condensed:ital,wght@0,400;0,700;1,400&display=swap">
<style>
  :root {
    --navy: #123f8e;
    --navy-deep: #0d3580;
    --sky: #7cc4f2;
    --orange: #f59a2f;
    --ink: #111111;
    --paper: #ffffff;
    --mist: #dfe4ea;
    --steel: #6d6e70;
    --stage: #d8d5d1;
  }
  * { box-sizing: border-box; margin: 0; padding: 0; }
  html, body { width: 1200px; height: 1000px; overflow: hidden; }
  body {
    background: var(--stage);
    font-family: "Roboto Condensed", "Arial Narrow", sans-serif;
    position: relative;
    color: var(--ink);
  }
  .flyer {
    position: absolute; left: 46px; top: 53px; width: 635px; height: 896px;
    background: linear-gradient(180deg, #eef1f4 0%, #dfe4ea 60%, #e6e9ed 100%);
    overflow: hidden;
  }
  .flyer__band { position: absolute; left: 0; top: 0; }
  .flyer__hero {
    position: absolute; left: 40px; top: 18px; width: 260px; height: 455px;
    background: linear-gradient(180deg, #c9a84a 0%, #3f6fb8 25%, #3866ad 60%, #8d6a42 85%, #9db1c8 100%);
    border-radius: 120px 120px 10px 10px;
  }
  .brand {
    position: absolute; text-align: center; color: var(--navy);
    font-weight: 700; text-transform: uppercase; line-height: 1;
  }
  .flyer .brand { left: 244px; top: 138px; width: 366px; font-size: 38px; letter-spacing: 1px; }
  .brand__dot { display: inline-block; width: 14px; height: 14px; border-radius: 50%; background: currentColor; margin-right: 10px; vertical-align: middle; }
  .flyer__photo {
    position: absolute; top: 305px; width: 176px; height: 133px;
    border: 5px solid var(--paper); box-shadow: 0 1px 3px rgba(0,0,0,.2);
  }
  .flyer__photo--work { left: 244px; background: linear-gradient(135deg, #dfe6ee 0%, #4d77b8 45%, #2d4f8c 70%, #c8d2de 100%); }
  .flyer__photo--pipe { left: 430px; background: linear-gradient(135deg, #e9edf1 0%, #b9c3cd 40%, #c7342e 60%, #d8b49a 80%, #eef1f4 100%); }
  .panel {
    position: absolute; top: 474px; width: 299px; height: 254px;
    background: var(--navy); border-radius: 16px; padding: 6px;
  }
  .panel--offer { left: 1px; }
  .panel--services { left: 336px; }
  .panel__inner {
    width: 100%; height: 100%; border: 1.5px dashed rgba(255,255,255,.8);
    border-radius: 12px; padding: 42px 10px 0 12px;
  }
  .panel__tab {
    position: absolute; top: -5px; height: 40px; padding: 0 9px;
    background: var(--orange); color: var(--paper); font-weight: 700;
    font-size: 27px; line-height: 40px; border-radius: 3px;
  }
  .panel--offer .panel__tab { left: 38px; }
  .panel--services .panel__tab { left: 38px; }
  .ticks { list-style: none; }
  .ticks li {
    position: relative; padding-left: 29px; color: var(--paper);
    font-size: 20px; line-height: 25px; margin-bottom: 24px;
  }
  .ticks li svg { position: absolute; left: 0; top: -2px; }
  .ticks b { font-weight: 700; }
  .ticks .lead { color: var(--sky); font-weight: 700; font-size: 22px; }
  .panel--services .ticks li { font-weight: 700; }
  .flyer__rule { position: absolute; left: 0; top: 778px; width: 635px; height: 6px; background: var(--navy); }
  .flyer__foot { position: absolute; left: 0; top: 784px; width: 635px; height: 112px; background: var(--paper); }
  .cta {
    position: absolute; left: 122px; top: 758px; width: 390px; height: 47px;
    background: var(--ink); color: var(--paper); border-radius: 6px;
    text-align: center; font-size: 16px; line-height: 20px; padding-top: 4px;
  }
  .cta em { font-style: normal; color: var(--sky); }
  .fineprint { position: absolute; left: 38px; top: 828px; font-size: 11px; line-height: 14px; font-style: italic; }
  .fineprint b { font-weight: 700; }
  .contact { position: absolute; left: 420px; top: 817px; width: 200px; text-align: center; }
  .contact__phone { font-size: 27px; font-weight: 700; line-height: 30px; display: flex; align-items: center; justify-content: center; gap: 6px; }
  .contact__line { font-size: 12px; line-height: 15px; }

  .card { position: absolute; left: 740px; width: 386px; height: 229px; box-shadow: 0 2px 4px rgba(0,0,0,.3); overflow: hidden; }
  .card--front { top: 247px; background: var(--navy); }
  .card--front .brand { left: 0; top: 100px; width: 386px; color: var(--paper); font-size: 30px; letter-spacing: 1px; }
  .card__services { position: absolute; left: 0; top: 198px; width: 386px; text-align: center; color: var(--paper); font-size: 12px; letter-spacing: .3px; }
  .card__services span { display: inline-block; width: 5px; height: 5px; border-radius: 50%; background: var(--sky); margin: 0 7px; vertical-align: middle; }
  .card--back { top: 534px; background: var(--paper); }
  .card--back .brand { left: 20px; top: 62px; width: 180px; text-align: left; font-size: 19px; }
  .card__contacts { position: absolute; left: 22px; top: 144px; list-style: none; font-size: 11px; line-height: 18px; }
  .card__contacts li { display: flex; align-items: center; gap: 6px; }
  .card__stripe { position: absolute; left: 0; bottom: 0; }
</style>
</head>
<body>

<section class="flyer" aria-label="Start up offer flyer">
  <svg class="flyer__band" width="635" height="896" viewBox="0 0 635 896" aria-hidden="true">
    <polygon points="0,190 65,190 65,310 0,345" fill="var(--navy)"/>
    <rect x="240" y="260" width="395" height="21" fill="var(--navy)"/>
  </svg>
  <div class="flyer__hero" role="img" aria-label="Smiling plumber in hard hat and blue polo with a tool belt, arms crossed"></div>

  <div class="brand">Danny Flow Plumbing</div>

  <div class="flyer__photo flyer__photo--work" role="img" aria-label="Plumber fixing pipes under a sink"></div>
  <div class="flyer__photo flyer__photo--pipe" role="img" aria-label="Hand tightening a chrome pipe with a red wrench"></div>

  <div class="panel panel--offer">
    <div class="panel__tab">Offer</div>
    <div class="panel__inner">
      <ul class="ticks">
        <li><svg width="24" height="24" viewBox="0 0 24 24"><path d="M2 13 l6 7 L22 2" fill="none" stroke="#fff" stroke-width="3.5" stroke-linecap="round" stroke-linejoin="round"/></svg><span class="lead">15% off your overall bill*</span></li>
        <li><svg width="24" height="24" viewBox="0 0 24 24"><path d="M2 13 l6 7 L22 2" fill="none" stroke="#fff" stroke-width="3.5" stroke-linecap="round" stroke-linejoin="round"/></svg>No GST payable, saving you <b>additional 10% on your bill</b> ^</li>
        <li><svg width="24" height="24" viewBox="0 0 24 24"><path d="M2 13 l6 7 L22 2" fill="none" stroke="#fff" stroke-width="3.5" stroke-linecap="round" stroke-linejoin="round"/></svg>Plus, a <b>FREE hot water health check</b> and replacement quote ~</li>
      </ul>
    </div>
  </div>

  <div class="panel panel--services">
    <div class="panel__tab">Services Offered</div>
    <div class="panel__inner">
      <ul class="ticks">
        <li><svg width="24" height="24" viewBox="0 0 24 24"><path d="M2 13 l6 7 L22 2" fill="none" stroke="#fff" stroke-width="3.5" stroke-linecap="round" stroke-linejoin="round"/></svg>All plumbing, draining, and gasfitting works</li>
        <li><svg width="24" height="24" viewBox="0 0 24 24"><path d="M2 13 l6 7 L22 2" fill="none" stroke="#fff" stroke-width="3.5" stroke-linecap="round" stroke-linejoin="round"/></svg>Quality work at a Decent Price</li>
        <li><svg width="24" height="24" viewBox="0 0 24 24"><path d="M2 13 l6 7 L22 2" fill="none" stroke="#fff" stroke-width="3.5" stroke-linecap="round" stroke-linejoin="round"/></svg>Local Plumber</li>
      </ul>
    </div>
  </div>

  <div class="flyer__rule"></div>
  <div class="flyer__foot"></div>
  <div class="cta">To make an appointment, <em>call or email Danny</em>,<br>or alternatively make a booking directly on the website</div>

  <p class="fineprint">*Offer valid between <b>15 August 2016 to 15 October 2016</b><br>^ Valid until <b>30 September 2016.</b><br>~ Quote valid for <b>12 months from the quote date.</b></p>

  <div class="contact">
    <div class="contact__phone">
      <svg width="22" height="22" viewBox="0 0 24 24" aria-hidden="true"><circle cx="12" cy="12" r="10.5" fill="none" stroke="var(--navy)" stroke-width="2"/><path d="M8.5 6.5 l2 2.5 -1.2 1.4 c.8 1.8 2 3 3.8 3.8 l1.4-1.2 2.5 2 -1.5 2 c-4.5-.5-8.3-4.3-8.8-8.8z" fill="var(--navy)"/></svg>
      0400 555 218
    </div>
    <div class="contact__line">danny@dannyflowplumbing.com</div>
    <div class="contact__line">www.dannyflowplumbing.com</div>
  </div>
</section>

<section class="card card--front" aria-label="Business card front">
  <div class="brand">Danny Flow Plumbing</div>
  <div class="card__services">PLUMBING<span></span>DRAINING<span></span>GASFITTING WORKS</div>
</section>

<section class="card card--back" aria-label="Business card back">
  <div class="brand">Danny Flow<br>Plumbing</div>
  <ul class="card__contacts">
    <li><svg width="10" height="10" viewBox="0 0 24 24" aria-hidden="true"><circle cx="12" cy="12" r="10.5" fill="none" stroke="var(--ink)" stroke-width="2.5"/><path d="M8.5 6.5 l2 2.5 -1.2 1.4 c.8 1.8 2 3 3.8 3.8 l1.4-1.2 2.5 2 -1.5 2 c-4.5-.5-8.3-4.3-8.8-8.8z" fill="var(--ink)"/></svg>0400 555 218</li>
    <li><svg width="10" height="10" viewBox="0 0 24 24" aria-hidden="true"><rect x="2" y="5" width="20" height="14" fill="none" stroke="var(--ink)" stroke-width="2.5"/><path d="M2 5 l10 8 10-8" fill="none" stroke="var(--ink)" stroke-width="2.5"/></svg>danny@dannyflowplumbing.com</li>
    <li><svg width="10" height="10" viewBox="0 0 24 24" aria-hidden="true"><circle cx="12" cy="12" r="10" fill="none" stroke="var(--ink)" stroke-width="2.5"/><path d="M2 12 h20 M12 2 c-5 6-5 14 0 20 M12 2 c5 6 5 14 0 20" fill="none" stroke="var(--ink)" stroke-width="2"/></svg>www.dannyflowplumbing.com</li>
  </ul>
  <svg class="card__stripe" width="386" height="22" viewBox="0 0 386 22" aria-hidden="true">
    <polygon points="0,0 200,0 191,22 0,22" fill="var(--navy)"/>
    <polygon points="200,0 386,0 386,22 191,22" fill="var(--steel)"/>
  </svg>
</section>

</body>
</html>
```